Facebook Post for Fence Spring Sale

We have a $12 / FT Fence sale that we have been running for a while now. We need a flyer made up for SPRING.

Our previous flyer can be seen here:
https://media-cdn4.pixvaultcloud.example/img/v2/58120947_302918475610234_1937465028364719205_n.jpg?k=7c2e91b04d3a58f6e2b7c1d9a0f46e83&t=72A19C04

We want to use the photos that are shown here https://files.boxmeadow.example/share?id=7QxLm2pRtKwZs9VnHyBcJdEf4Ga in the flyer. This is to be posted on Facebook so it must be the proper size for Facebook page post.

The wording to be used should be "Spring Fence Sale" and "$12 / FT Wood Fences" Also we should include our business name "Oakvale Fence" and phone number for Free Estimates - 555-216-4073.

Industry/Entity Type

Residential Construction

Font styles to use
Serif
Sans Serif

Colors
3176b5
fbee3d
fbed22
fbf289
85cae6
33a6d7

Requirements
Must have
• Phone number, $12 / FT Fence Sale

```html
<!DOCTYPE html>
<html lang="en">
<head>
<meta charset="utf-8">
<title>Oakvale Fence – Spring Fence Sale</title>
<link rel="stylesheet" href="https://fonts.googleapis.com/css2?family=Roboto+Condensed:ital,wght@0,700;1,700&family=Arimo:wght@700&display=swap">
<style>
  :root {
    --page: #ffffff;
    --lime: #b5d334;
    --lime-light: #e3ef86;
    --lime-deep: #9cc22b;
    --forest: #0f5a2c;
    --band-light: #8cc63f;
    --phone: #fbed22;
    --white: #ffffff;
    --grass: #5f8f2e;
    --wood: #c9b27a;
  }
  * { margin: 0; padding: 0; box-sizing: border-box; }
  html, body {
    width: 1200px; height: 1130px; overflow: hidden;
    background: var(--page);
  }
  .flyer {
    position: absolute; left: 150px; top: 112px;
    width: 900px; height: 905px;
    overflow: hidden;
    background: var(--lime);
    box-shadow: 0 6px 24px rgba(0,0,0,0.35);
  }
  .header {
    position: absolute; left: 0; top: 0; width: 900px; height: 259px;
  }
  .header-art {
    position: absolute; inset: 0;
    background: linear-gradient(150deg, var(--lime-light) 0%, var(--lime) 45%, var(--lime-deep) 100%);
  }
  .title {
    position: absolute; width: 900px; text-align: center;
    font-family: "Roboto Condensed", "Arial Narrow", sans-serif;
    font-style: italic; font-weight: 700; line-height: 1;
    white-space: nowrap;
  }
  .title-brand {
    top: 22px; left: 18px; font-size: 106px; letter-spacing: 2px;
    color: var(--white);
    text-shadow: 2px 3px 4px rgba(0,0,0,0.45);
  }
  .title-sale {
    top: 134px; left: 0; font-size: 106px; letter-spacing: 3px;
    color: var(--forest);
    text-shadow: 1px 2px 2px rgba(255,255,255,0.35);
  }
  .photo-row {
    position: absolute; left: 0; top: 262px; width: 900px; height: 217px;
    display: flex; gap: 8px; background: var(--lime);
  }
  .photo-row .photo { flex: 1; height: 100%; }
  .photo-gate { background: linear-gradient(180deg, #cfc6a8, #b9a980 60%, #7a7058); }
  .photo-scallop { background: linear-gradient(180deg, #c7d3cf, #c8a66a 40%, #6c8b3a); }
  .photo-privacy { background: linear-gradient(180deg, #8fb4d6, #d1b27a 45%, #8a7044); }
  .photo-rail { background: linear-gradient(180deg, #4d7a33, #d7cf9a 50%, #7ea24a); }
  .hero {
    position: absolute; left: 0; top: 487px; width: 900px; height: 360px;
    background: linear-gradient(180deg, #7ea860 0%, var(--grass) 35%, var(--wood) 55%, #8f7a4c 80%, var(--grass) 100%);
  }
  .offer {
    position: absolute; right: 48px; text-align: right; white-space: nowrap;
    font-family: "Arimo", Arial, sans-serif; font-weight: 700; line-height: 1;
    color: var(--white);
    text-shadow: 2px 2px 3px rgba(0,0,0,0.75);
  }
  .offer-price { top: 515px; font-size: 75px; }
  .offer-estimates {
    top: 600px; font-size: 58px;
    font-family: "Roboto Condensed", "Arial Narrow", sans-serif;
  }
  .contact {
    position: absolute; left: 66px; top: 688px;
    display: flex; align-items: center; gap: 22px;
  }
  .contact svg { width: 98px; height: 98px; filter: drop-shadow(2px 2px 2px rgba(0,0,0,0.6)); }
  .contact-phone {
    font-family: "Arimo", Arial, sans-serif; font-weight: 700;
    font-size: 108px; line-height: 1; color: var(--phone);
    letter-spacing: -1px; white-space: nowrap;
    text-shadow: 3px 3px 3px rgba(0,0,0,0.7);
  }
  .web-band {
    position: absolute; left: 0; top: 836px; width: 900px; height: 52px;
    background: rgba(31,104,44,0.9);
    text-align: center;
    font-family: "Arimo", Arial, sans-serif; font-weight: 700;
    font-size: 38px; line-height: 52px; color: var(--white);
  }
  .base-strip {
    position: absolute; left: 0; top: 888px; width: 900px; height: 17px;
    background: var(--band-light);
  }
</style>
</head>
<body>
  <main class="flyer">
    <header class="header">
      <div class="header-art" role="img" aria-label="Spring sun with rays over lime green background"></div>
      <h1 class="title title-brand">Oakvale Fence</h1>
      <h2 class="title title-sale">Spring Fence Sale</h2>
    </header>

    <section class="photo-row">
      <div class="photo photo-gate" role="img" aria-label="Wooden picket gate with black hinges"></div>
      <div class="photo photo-scallop" role="img" aria-label="Scalloped wood picket fence beside a sidewalk"></div>
      <div class="photo photo-privacy" role="img" aria-label="Wood privacy fence with wavy top"></div>
      <div class="photo photo-rail" role="img" aria-label="Arched picket gate on split rail fence"></div>
    </section>

    <div class="hero" role="img" aria-label="Dog-ear wood picket fence on green lawn"></div>

    <p class="offer offer-price">$12 / FT Wood Fences</p>
    <p class="offer offer-estimates">Free Estimates</p>

    <div class="contact">
      <svg viewBox="0 0 100 100" aria-hidden="true">
        <circle cx="50" cy="50" r="42" fill="none" stroke="var(--phone)" stroke-width="7"/>
        <path d="M36 26c4-2 7 0 9 5l3 7c1 3 0 5-2 7l-3 2c2 6 7 11 13 14l2-3c2-2 4-3 7-2l7 3c5 2 6 5 4 9l-3 5c-3 4-10 4-17 0-11-6-20-15-25-26-4-8-3-15 1-18z" fill="var(--phone)"/>
      </svg>
      <span class="contact-phone">555-216-4073</span>
    </div>

    <div class="web-band">www.MyOakvaleFence.com</div>
    <div class="base-strip"></div>
  </main>
</body>
</html>
```